Mobile app for checking bus arrival

I would like to make the UI much more beautiful and modern. The app is an app to check bus arrival in Singapore.
See here: https://apps.veltrano.com/store/apps/details?id=com.ridoka&hl=en

Based on the question from designers:

1. The first screen shows the favorite bus stop. Each item shows location / street, the top one is the location, second line is the street name. And the number is the bus stop code.

2. Please download the app and try bus stop code with 07589 or 10079, for example. It will bring you to the next screen.

3. The pencil allow you to select color theme, for the list item, and the header.

4. On the second screen, it will show up the list of bus route that available on that bus stop.

5. When you tap on one of them it will show you the 2 subsequent arrival time.

6. Each of the arrival time has the information of availability seats available, seats not available, no more space. (we can use green, yellow, red, respectively).

7. Each of the arrival time has the WAB indicator (Wheelchair availability). Show as icon is preferred.

7. KLT and VOPN are the bus provider in Singapore. 48 means the route /service no.

Requirements:
And check the attachment, see screen 3. I need to add information about the space availability, which has 3 state: seats available, seats not available, no more space. (we can use green, yellow, red, respectively).

Please advise how to show the information.

Target Market(s)

Students, age below 35

Industry/Entity Type

Trivex

Requirements
Must have
• The app currently has the capabilities to select color theme, checkout screen1. It's the button and the list item color.
Nice to have
• Please download the app to see all available colors, and make suggestion to have better color pallete.

```html
<!DOCTYPE html>
<html lang="en">
<head>
<meta charset="utf-8">
<title>Bus Stop Code – Favourites</title>
<link rel="stylesheet" href="https://fonts.googleapis.com/css2?family=Open+Sans:ital,wght@0,400;0,600;1,400&display=swap">
<style>
  :root {
    --header-blue: #5a80ee;
    --search-blue: #4264c8;
    --card-blue: #5a80f0;
    --code-blue: #4a6fe0;
    --star: #f9b92a;
    --fab-green: #2fb52a;
    --white: #ffffff;
    --divider: #d6d6d6;
    --ad-frame: #3a3a3a;
    --ad-gold-1: #6b3c12;
    --ad-gold-2: #d89a2c;
  }
  * { box-sizing: border-box; margin: 0; padding: 0; }
  html, body { width: 676px; height: 1200px; overflow: hidden; background: var(--white); }
  body { position: relative; font-family: "Open Sans", Arial, sans-serif; color: var(--white); }

  .app-header { position: absolute; left: 0; top: 0; width: 676px; height: 135px; background: var(--header-blue); }
  .status-bar { position: absolute; left: 0; top: 0; width: 676px; height: 42px; font-size: 22px; }
  .status-bar .carrier { position: absolute; left: 12px; top: 8px; display: flex; align-items: center; gap: 6px; }
  .status-bar .time { position: absolute; left: 0; right: 0; top: 8px; text-align: center; font-weight: 600; }
  .status-bar .battery { position: absolute; right: 12px; top: 8px; display: flex; align-items: center; gap: 8px; }

  .menu-button { position: absolute; left: 35px; top: 74px; }
  .search-field { position: absolute; left: 98px; top: 59px; width: 542px; height: 64px; background: var(--search-blue); }
  .search-field .title { position: absolute; left: 0; right: 0; top: 13px; text-align: center; font-style: italic; font-size: 31px; line-height: 38px; }
  .search-field svg { position: absolute; right: 10px; top: 18px; }

  .stop-card { position: absolute; left: 34px; width: 608px; height: 95px; border-radius: 7px; overflow: hidden; background: var(--card-blue); display: flex; }
  .stop-card .code { width: 99px; height: 100%; background: var(--code-blue); font-size: 23px; display: flex; align-items: center; justify-content: center; }
  .stop-card .info { position: relative; flex: 1; padding: 18px 0 0 18px; }
  .stop-card .name { font-size: 31px; line-height: 36px; display: flex; align-items: center; gap: 6px; white-space: nowrap; }
  .stop-card .street { font-size: 23px; line-height: 28px; padding-left: 28px; white-space: nowrap; }
  .stop-card .star { position: absolute; right: 18px; top: 24px; }

  .list-end { position: absolute; left: 34px; top: 738px; width: 608px; height: 1px; background: var(--divider); }

  .edit-theme { position: absolute; left: 548px; top: 953px; width: 74px; height: 74px; border-radius: 50%; background: var(--fab-green); display: flex; align-items: center; justify-content: center; }

  .ad-banner { position: absolute; left: 0; top: 1108px; width: 676px; height: 92px; background: var(--ad-frame); border-top: 1px solid #555; overflow: hidden; }
  .ad-banner .ad-art { position: absolute; left: 38px; top: 0; width: 600px; height: 92px; background: linear-gradient(90deg, var(--ad-gold-1), var(--ad-gold-2) 55%, var(--ad-gold-1)); }
  .ad-banner .ad-size { position: absolute; left: 62px; top: 6px; font-size: 33px; line-height: 40px; color: var(--white); white-space: nowrap; }
  .ad-banner .ad-brand { position: absolute; left: 340px; top: 20px; height: 50px; display: flex; align-items: center; gap: 14px; color: var(--white); white-space: nowrap; }
  .ad-banner .ad-brand i { display: block; width: 44px; height: 48px; background: var(--white); }
  .ad-banner .ad-brand .ad-name { font-size: 36px; line-height: 44px; }
  .ad-banner .ad-brand .ad-by { font-size: 14px; line-height: 14px; align-self: flex-end; margin: 0 0 8px -8px; }
  .ad-banner .ad-info { position: absolute; left: 6px; top: 64px; }
</style>
</head>
<body>
  <header class="app-header">
    <div class="status-bar">
      <div class="carrier">
        <svg width="70" height="14" viewBox="0 0 70 14"><g fill="#fff"><circle cx="7" cy="7" r="6"/><circle cx="21" cy="7" r="6"/><circle cx="35" cy="7" r="6"/></g><g fill="none" stroke="#fff" stroke-width="1.5"><circle cx="49" cy="7" r="5.5"/><circle cx="63" cy="7" r="5.5"/></g></svg>
        <span>KESTO</span>
        <svg width="24" height="18" viewBox="0 0 24 18"><g fill="none" stroke="#fff" stroke-width="2.6" stroke-linecap="round"><path d="M2 6a14 14 0 0 1 20 0"/><path d="M6 10a8 8 0 0 1 12 0"/></g><circle cx="12" cy="15" r="2.2" fill="#fff"/></svg>
      </div>
      <div class="time">4:21 PM</div>
      <div class="battery">
        <svg width="14" height="22" viewBox="0 0 14 22"><path d="M2 6l10 10-5 5V1l5 5L2 16" fill="none" stroke="#c9d6ff" stroke-width="1.6"/></svg>
        <span>22%</span>
        <svg width="46" height="20" viewBox="0 0 46 20"><rect x="1" y="1" width="40" height="18" rx="3" fill="none" stroke="#fff" stroke-width="1.6"/><rect x="4" y="4" width="8" height="12" fill="#fff"/><rect x="42" y="6" width="3" height="8" fill="#fff"/></svg>
      </div>
    </div>
    <svg class="menu-button" width="35" height="34" viewBox="0 0 35 34"><g stroke="#fff" stroke-width="2.4"><line x1="0" y1="2" x2="35" y2="2"/><line x1="0" y1="17" x2="35" y2="17"/><line x1="0" y1="32" x2="35" y2="32"/></g></svg>
    <div class="search-field">
      <div class="title">Bus Stop Code</div>
      <svg width="30" height="30" viewBox="0 0 30 30"><circle cx="12" cy="12" r="9" fill="none" stroke="#fff" stroke-width="3"/><line x1="19" y1="19" x2="28" y2="28" stroke="#fff" stroke-width="3.4" stroke-linecap="round"/></svg>
    </div>
  </header>

  <main>
    <article class="stop-card" style="top:157px">
      <div class="code">09022</div>
      <div class="info">
        <div class="name"><svg width="22" height="30" viewBox="0 0 22 30"><path d="M11 1a10 10 0 0 0-10 10c0 7 10 18 10 18s10-11 10-18A10 10 0 0 0 11 1z" fill="#fff"/><circle cx="11" cy="11" r="3.6" fill="var(--card-blue)"/></svg>Opp Orchard stn</div>
        <div class="street">orchard boulevard</div>
        <svg class="star" width="42" height="40" viewBox="0 0 42 40"><path d="M21 1l6 13 14 1.5-10.5 9.5 3 14L21 32 8.5 39l3-14L1 15.5 15 14z" fill="var(--star)"/></svg>
      </div>
    </article>
    <article class="stop-card" style="top:278px">
      <div class="code">10079</div>
      <div class="info">
        <div class="name"><svg width="22" height="30" viewBox="0 0 22 30"><path d="M11 1a10 10 0 0 0-10 10c0 7 10 18 10 18s10-11 10-18A10 10 0 0 0 11 1z" fill="#fff"/><circle cx="11" cy="11" r="3.6" fill="var(--card-blue)"/></svg>Blk 201</div>
        <div class="street">jln bt merah</div>
        <svg class="star" width="42" height="40" viewBox="0 0 42 40"><path d="M21 1l6 13 14 1.5-10.5 9.5 3 14L21 32 8.5 39l3-14L1 15.5 15 14z" fill="var(--star)"/></svg>
      </div>
    </article>
    <article class="stop-card" style="top:401px">
      <div class="code">18141</div>
      <div class="info">
        <div class="name"><svg width="22" height="30" viewBox="0 0 22 30"><path d="M11 1a10 10 0 0 0-10 10c0 7 10 18 10 18s10-11 10-18A10 10 0 0 0 11 1z" fill="#fff"/><circle cx="11" cy="11" r="3.6" fill="var(--card-blue)"/></svg>Aft anglo-chinese jc</div>
        <div class="street">north bouna vista rd</div>
        <svg class="star" width="42" height="40" viewBox="0 0 42 40"><path d="M21 1l6 13 14 1.5-10.5 9.5 3 14L21 32 8.5 39l3-14L1 15.5 15 14z" fill="var(--star)"/></svg>
      </div>
    </article>
    <article class="stop-card" style="top:523px">
      <div class="code">66081</div>
      <div class="info">
        <div class="name"><svg width="22" height="30" viewBox="0 0 22 30"><path d="M11 1a10 10 0 0 0-10 10c0 7 10 18 10 18s10-11 10-18A10 10 0 0 0 11 1z" fill="#fff"/><circle cx="11" cy="11" r="3.6" fill="var(--card-blue)"/></svg>Opp s’pore po..</div>
        <div class="street">bladdell rd</div>
        <svg class="star" width="42" height="40" viewBox="0 0 42 40"><path d="M21 1l6 13 14 1.5-10.5 9.5 3 14L21 32 8.5 39l3-14L1 15.5 15 14z" fill="var(--star)"/></svg>
      </div>
    </article>
    <article class="stop-card" style="top:643px">
      <div class="code">08031</div>
      <div class="info">
        <div class="name"><svg width="22" height="30" viewBox="0 0 22 30"><path d="M11 1a10 10 0 0 0-10 10c0 7 10 18 10 18s10-11 10-18A10 10 0 0 0 11 1z" fill="#fff"/><circle cx="11" cy="11" r="3.6" fill="var(--card-blue)"/></svg>Dhob…</div>
        <div class="street">penang rd</div>
        <svg class="star" width="42" height="40" viewBox="0 0 42 40"><path d="M21 1l6 13 14 1.5-10.5 9.5 3 14L21 32 8.5 39l3-14L1 15.5 15 14z" fill="var(--star)"/></svg>
      </div>
    </article>
    <div class="list-end"></div>

    <div class="edit-theme">
      <svg width="34" height="34" viewBox="0 0 34 34"><path d="M17 5H5v24h24V17" fill="none" stroke="#fff" stroke-width="3"/><path d="M27 3l4 4-13 13-5 1 1-5z" fill="#fff"/></svg>
    </div>
  </main>

  <footer class="ad-banner">
    <div class="ad-art" role="img" aria-label="Test advertisement banner artwork in warm gold tones"></div>
    <div class="ad-size">320x50<br>Test Banner</div>
    <div class="ad-brand"><i></i><span class="ad-name">AdReach</span><span class="ad-by">by Trivex</span></div>
    <svg class="ad-info" width="24" height="24" viewBox="0 0 24 24"><circle cx="12" cy="12" r="10" fill="none" stroke="#bbb" stroke-width="2"/><rect x="11" y="10" width="2.4" height="8" fill="#bbb"/><circle cx="12.2" cy="7" r="1.5" fill="#bbb"/></svg>
  </footer>
</body>
</html>
```